Podiatry (services) Business Card

I need a business design for a New Podiatry Service.
the Podiatry services will include all aspects of podiatry including;
general podiatry for all ages
corns and callus treatment
Ingrown toenails & nail surgery
Forefoot, arch and heel pain
Gait analysis
Sports Podiatry and Orthotics
Paediatric Assessments
Diabetes Foot Assessment

I would like the back of the card to have space for next appointment day and time.

I would like a nice design that is simple yet catchy. I don't like cluttered business cards. I like things to be simple yet stand out because of the finer details.

I like the colours blue and white but I'm open to other designs that have different colours.

Business

Bluewren Podiatry (Business name)

Marisol Tenbury - Podiatrist
M.Pod.P., B.Hlth. Sci, MFLsoc

Address: 58 Coleby St, Marrowdale North Vic, 3164
Phone: (03) 9416 2738
Fax: (03) 9523 4178

```html
<!DOCTYPE html>
<html lang="en">
<head>
<meta charset="utf-8">
<title>Bluewren Podiatry – Business Card</title>
<link href="https://fonts.googleapis.com/css2?family=Source+Sans+3:wght@400;600;700&display=swap" rel="stylesheet">
<style>
  :root {
    --brand-blue: #1a78c2;
    --card-white: #ffffff;
    --ink-dark: #1d1d1d;
    --backdrop: #e9ecef;
  }
  * { box-sizing: border-box; margin: 0; padding: 0; }
  html, body {
    width: 1200px; height: 900px; overflow: hidden;
    background: var(--backdrop);
    font-family: "Source Sans 3", "Myriad Pro", Arial, sans-serif;
  }
  .card {
    position: absolute;
    background: var(--card-white);
    overflow: hidden;
    box-shadow: 0 6px 18px rgba(0,0,0,0.18);
  }
  .card-band { position: absolute; inset: 0; width: 100%; height: 100%; }

  /* Front */
  .card-front { left: 78px; top: 35px; width: 587px; height: 362px; }
  .brand {
    position: absolute; left: 92px; top: 52px;
    display: flex; align-items: center; gap: 18px;
  }
  .brand-dot { width: 46px; height: 46px; border-radius: 50%; background: var(--brand-blue); }
  .brand-name {
    font-size: 40px; font-weight: 400; color: var(--brand-blue);
    letter-spacing: 1px; line-height: 1;
  }
  .contact-lines {
    position: absolute; right: 330px; top: 250px;
    color: var(--card-white); font-size: 16px; line-height: 25px; text-align: right;
  }
  .contact-line { display: flex; align-items: center; justify-content: flex-end; gap: 6px; }
  .contact-line svg { width: 11px; height: 11px; fill: var(--card-white); }
  .practitioner {
    position: absolute; left: 290px; top: 213px;
    color: var(--card-white);
  }
  .practitioner-name { font-size: 21px; font-weight: 700; line-height: 1.2; }
  .practitioner-role { font-size: 16px; font-weight: 400; }
  .credentials { font-size: 15.5px; line-height: 22px; }
  .address { margin-top: 13px; font-size: 16px; line-height: 24px; }

  /* Back */
  .card-back { left: 388px; top: 505px; width: 567px; height: 352px; }
  .appointment {
    position: absolute; left: 0; right: 0; top: 18px;
    text-align: center; color: var(--brand-blue);
  }
  .appointment-title { font-size: 20px; font-weight: 700; letter-spacing: 0.5px; }
  .appointment-field {
    font-size: 16px; font-weight: 600; margin-top: 18px;
  }
  .appointment-field .dots { color: var(--ink-dark); font-weight: 400; letter-spacing: 0.5px; }
  .appointment-field + .appointment-field { margin-top: 30px; }
  .services {
    position: absolute; left: 0; right: 0; top: 202px;
    text-align: center; color: var(--card-white);
  }
  .services-title { font-size: 20px; font-weight: 700; margin-bottom: 8px; }
  .services-row { font-size: 16px; font-weight: 600; line-height: 23.5px; }
  .services-row .sep { margin: 0 8px; font-weight: 400; }
</style>
</head>
<body>

<section class="card card-front" aria-label="Business card front">
  <svg class="card-band" viewBox="0 0 587 362" preserveAspectRatio="none" aria-hidden="true">
    <polygon points="0,173 388,173 413,165 587,165 587,362 0,362" fill="var(--brand-blue)"/>
    <polyline points="0,200 392,200 415,165" fill="none" stroke="#ffffff" stroke-width="2.2"/>
  </svg>

  <div class="brand">
    <span class="brand-dot"></span>
    <span class="brand-name">Bluewren Podiatry</span>
  </div>

  <div class="contact-lines">
    <div class="contact-line">(03) 9416 2738
      <svg viewBox="0 0 24 24"><path d="M6.6 10.8a15.1 15.1 0 0 0 6.6 6.6l2.2-2.2c.3-.3.7-.4 1-.2 1.1.4 2.3.6 3.6.6.6 0 1 .4 1 1V20c0 .6-.4 1-1 1C10.6 21 3 13.4 3 4c0-.6.4-1 1-1h3.5c.6 0 1 .4 1 1 0 1.3.2 2.5.6 3.6.1.3 0 .7-.2 1z"/></svg>
    </div>
    <div class="contact-line">(03) 9523 4178
      <svg viewBox="0 0 24 24"><path d="M6 2h9l3 3v5h2a2 2 0 0 1 2 2v8a2 2 0 0 1-2 2H4a2 2 0 0 1-2-2v-8a2 2 0 0 1 2-2h2zm2 2v6h8V6h-2V4zM6 14v2h3v-2zm5 0v2h3v-2zm5 0v2h3v-2z"/></svg>
    </div>
  </div>

  <div class="practitioner">
    <div class="practitioner-name">Marisol Tenbury <span class="practitioner-role">- Podiatrist</span></div>
    <div class="credentials">M.Pod.P., B.Hlth. Sci, MFLsoc</div>
    <div class="address">58 Coleby St, Marrowdale<br>North Vic, 3164</div>
  </div>
</section>

<section class="card card-back" aria-label="Business card back">
  <svg class="card-band" viewBox="0 0 567 352" preserveAspectRatio="none" aria-hidden="true">
    <polygon points="0,163 340,163 352,155 567,155 567,352 0,352" fill="var(--brand-blue)"/>
    <polyline points="0,188 322,188 352,155" fill="none" stroke="#ffffff" stroke-width="2.2"/>
  </svg>

  <div class="appointment">
    <div class="appointment-title">APPOINTMENT</div>
    <div class="appointment-field">Name: <span class="dots">..........................................................</span></div>
    <div class="appointment-field">Date: <span class="dots">.........................</span> Time: <span class="dots">...........................</span></div>
  </div>

  <div class="services">
    <div class="services-title">SERVICES:</div>
    <div class="services-row">General podiatry for all ages<span class="sep">|</span>Corns and callus treatment</div>
    <div class="services-row">Ingrown toenails &amp; nail surgery<span class="sep">|</span>Forefoot, arch and heel pain</div>
    <div class="services-row">Gait analysis<span class="sep">|</span>Sports Podiatry and Orthotics</div>
    <div class="services-row">Paediatric Assessments<span class="sep">|</span>Diabetes Foot Assessment</div>
  </div>
</section>

</body>
</html>
```